Pepper & Palm Business Card FUN & EXCITING

Here is the Information for the Card:
Jaswinder Bains (Ravi)
E: RaviBains@postlark.com
C: (480) 555-0147
www.PepperPalmLV.com

We don't want traditional Indian cliche, We a playful bold and fun business card.

Files: https://files.cloudvessel.net/share/folders/7TqRmXpZ2vKa9LwBn4YcHd3JsEf6UoGi?usp=share_link

https://files.cloudvessel.net/share/folders/4MzXaQ8rTw2YbNcVk6PsLe5GhJdR3FoU?usp=share_link

Target Market(s)

Las Vegas Local Restaurant

Industry/Entity Type

Indian Restaurant

Contact Information for Business Card

Name, Email, Cell Phone, Company Logo

```html
<!DOCTYPE html>
<html lang="en">
<head>
<meta charset="utf-8">
<title>Pepper &amp; Palm — Business Card</title>
<link rel="stylesheet" href="https://fonts.googleapis.com/css2?family=Oswald:wght@700&family=Open+Sans:wght@400;600&display=swap">
<style>
  :root {
    --stage: #232323;
    --card-white: #f4f2ef;
    --brand-pink: #e0175a;
    --brand-teal: #17a98d;
    --ink: #1c1c1c;
    --front-warm-1: #d9a58e;
    --front-warm-2: #c9b08a;
    --front-green: #b9c29a;
    --back-cream-1: #efe6d2;
    --back-cream-2: #f3ead0;
    --back-grey: #e7e4e0;
  }
  * { box-sizing: border-box; margin: 0; padding: 0; }
  html, body { width: 1200px; height: 780px; overflow: hidden; }
  body {
    background: var(--stage);
    display: flex;
    align-items: center;
    justify-content: center;
    gap: 90px;
    font-family: "Open Sans", Arial, sans-serif;
  }
  .card {
    position: relative;
    width: 380px;
    height: 640px;
    background: var(--card-white);
    overflow: hidden;
  }
  .card--front { border-radius: 190px 0 190px 0; }
  .card--back  { border-radius: 0 190px 0 190px; }

  .card__photo {
    position: absolute;
    inset: 0;
  }
  .card--front .card__photo {
    background:
      radial-gradient(circle at 60% 25%, rgba(232,170,180,.55), transparent 45%),
      radial-gradient(circle at 40% 55%, var(--front-green), transparent 55%),
      linear-gradient(160deg, var(--front-warm-1), var(--front-warm-2) 55%, var(--front-warm-1));
    opacity: .7;
  }
  .card--back .card__photo {
    background:
      radial-gradient(circle at 65% 45%, rgba(240,215,130,.7), transparent 30%),
      radial-gradient(ellipse at 60% 50%, var(--back-cream-2), var(--back-cream-1) 45%, var(--back-grey) 70%);
    opacity: .85;
  }

  .brand-name {
    font-family: "Oswald", "Arial Narrow", sans-serif;
    font-weight: 700;
    color: var(--brand-pink);
    text-transform: uppercase;
    line-height: 1;
    white-space: nowrap;
  }
  .card--front .brand-name {
    position: absolute;
    left: 50%;
    top: 50%;
    font-size: 72px;
    letter-spacing: 2px;
    transform: translate(-50%, -50%) rotate(-90deg);
  }
  .card--back .brand-name {
    position: absolute;
    top: 70px;
    left: 0;
    right: 0;
    text-align: center;
    font-size: 46px;
    letter-spacing: 1px;
  }

  .contact {
    position: absolute;
    left: 0;
    right: 0;
    top: 300px;
    text-align: center;
    color: var(--ink);
  }
  .contact__name {
    font-family: "Oswald", "Arial Narrow", sans-serif;
    font-weight: 700;
    font-size: 30px;
    color: var(--brand-pink);
    text-transform: uppercase;
    letter-spacing: .5px;
  }
  .contact__icons {
    display: flex;
    justify-content: center;
    gap: 8px;
    margin: 14px 0 10px;
  }
  .icon {
    width: 28px;
    height: 28px;
    border-radius: 50%;
    background: var(--brand-teal);
    display: flex;
    align-items: center;
    justify-content: center;
  }
  .icon svg { width: 16px; height: 16px; }
  .contact__line { font-size: 17px; line-height: 1.4; }
  .contact__pin { margin: 18px auto 8px; }
  .contact__address { font-size: 16px; line-height: 1.4; }
</style>
</head>
<body>

  <section class="card card--front" aria-label="Card front">
    <div class="card__photo" role="img" aria-label="Faded photo of a grilled curry dish topped with fresh herbs and sliced onion"></div>
    <h1 class="brand-name">Pepper &amp; Palm</h1>
  </section>

  <section class="card card--back" aria-label="Card back">
    <div class="card__photo" role="img" aria-label="Faded photo of a creamy dessert bowl garnished with a yellow flower"></div>
    <h2 class="brand-name">Pepper &amp; Palm</h2>

    <div class="contact">
      <p class="contact__name">Jaswinder Bains (Ravi)</p>
      <div class="contact__icons">
        <span class="icon" aria-label="Phone">
          <svg viewBox="0 0 24 24" fill="#fff"><path d="M6.6 10.8a15.5 15.5 0 0 0 6.6 6.6l2.2-2.2a1 1 0 0 1 1-.25 11.4 11.4 0 0 0 3.6.57 1 1 0 0 1 1 1V20a1 1 0 0 1-1 1A17 17 0 0 1 3 4a1 1 0 0 1 1-1h3.5a1 1 0 0 1 1 1c0 1.25.2 2.45.57 3.6a1 1 0 0 1-.25 1z"/></svg>
        </span>
        <span class="icon" aria-label="Email">
          <svg viewBox="0 0 24 24" fill="none" stroke="#fff" stroke-width="2"><rect x="3" y="5" width="18" height="14" rx="1.5"/><path d="M3 6l9 7 9-7"/></svg>
        </span>
        <span class="icon" aria-label="Website">
          <svg viewBox="0 0 24 24" fill="none" stroke="#fff" stroke-width="1.8"><circle cx="12" cy="12" r="9"/><path d="M3 12h18M12 3c2.5 2.7 2.5 15.3 0 18M12 3c-2.5 2.7-2.5 15.3 0 18"/></svg>
        </span>
      </div>
      <p class="contact__line">(480) 555-0147</p>
      <p class="contact__line">RaviBains@postlark.com</p>
      <p class="contact__line">www.PepperPalmLV.com</p>

      <span class="icon contact__pin" aria-label="Address">
        <svg viewBox="0 0 24 24" fill="none" stroke="#fff" stroke-width="2"><path d="M12 21s-6-6.2-6-11a6 6 0 0 1 12 0c0 4.8-6 11-6 11z"/><circle cx="12" cy="10" r="2.2"/></svg>
      </span>
      <p class="contact__address">1180 Desert Bloom Pkwy, Suite #210,<br>Henderson, NV 89000</p>
    </div>
  </section>

</body>
</html>
```